Luxury Real Estate Website, Midwest, United States

We need web design services for a luxury website. We need IDX Integration with our MLS. We want this to be a very simple website with amazing graphics. We want it to link up with our Postbird account in order to generate leads through a "More Information" Pop up on the main page. We want the main page to be covered with one large graphic that is a rolling slideshow of active listings of $400,000 and up from the IDX Integration. We need this website to give a very exclusive and sleek look. Lots of black is good... I will upload our logos in Black and Silver. We will also need an "About" page that we are going to call "Qeno Info". We want our graphics to be extremely impressive. Keep in mind, we are a company in the Midwest of the United States, and our real estate has a different look than homes in California or Florida. We need graphics that are realistic for the Midwest, yet still high-end.
Target Market(s)
Luxury Homeowners in the Midwest United States. The graphics needs to be pristine.
Industry/Entity Type
Real Estate
Coding
Coded - Design and coding required
Number of Pages Required
3 page
Requirements
Must have
- Large graphics with IDX Integration. The photos of real estate need to represent real estate that is common in the Midwest, United States. We also need Postbird integration. We need a pop up that is titled "My Free Market Analysis" that makes them fill out a contact form asking for Full Name, Email Address, Phone Number and Address. This needs to be a pop up on the front page and will integrate with our Postbird account. We also need a page called "About Qe No Home". And another page where clients can download informational PDFs. The main component needs to be a front page search engine connected with the IDX to access active listings from our MLS. I attached our logos and a sample front page of a website. I would love for ours to look similar.
Nice to have
- Lake House photos on midwest lakes are a plus.
Should not have
- Should not have clutter. This website needs to be clean, luxurious and exclusive.

```html
<!DOCTYPE html>
<html lang="en">
<head>
<meta charset="utf-8">
<title>Hearthstone Realty Group</title>
<link href="https://fonts.googleapis.com/css2?family=Questrial&display=swap" rel="stylesheet">
<style>
:root{
  --ink:#111111;
  --ink-soft:#1c1c1c;
  --white:#ffffff;
  --silver:#c9c9c9;
  --muted:#9a9a9a;
  --body-text:#a8a8a8;
  --nav-bar:rgba(8,8,8,.78);
  --field-line:#555555;
  --button-blue:#b7c7de;
  --footer-bg:#111111;
  --footer-text:#8e8e8e;
  --rule:#2e2e2e;
}
*{margin:0;padding:0;box-sizing:border-box}
html,body{width:1200px;height:2514px;overflow:hidden;background:var(--white)}
body{position:relative;font-family:"Questrial",sans-serif;color:var(--muted)}
.abs{position:absolute}

/* hero */
.hero{left:0;top:0;width:1200px;height:726px;background:linear-gradient(180deg,#6f6c66 0%,#66604f 35%,#55593f 62%,#46503a 85%,#4f5a40 100%)}
.hero-curve{left:0;top:590px;width:1200px;height:140px}
.site-header{left:0;top:0;width:1200px;height:112px;background:var(--nav-bar)}
.brand{left:99px;top:48px;color:var(--white);font-size:22px;letter-spacing:1px;display:flex;align-items:center;gap:10px}
.brand-mark{width:12px;height:12px;background:var(--silver)}
.main-nav a{position:absolute;top:56px;color:#d4d4d4;font-size:13px;text-decoration:none;letter-spacing:.5px;white-space:nowrap}
.main-nav a.current{color:var(--white)}
.main-nav a.current::after{content:"";position:absolute;left:0;right:0;bottom:-10px;height:2px;background:var(--silver)}
.slide-arrow{top:396px;width:20px;height:32px}

/* popup */
.analysis-popup{left:141px;top:251px;width:918px;height:292px;background:var(--ink);box-shadow:0 10px 40px rgba(0,0,0,.45)}
.popup-title{left:0;width:918px;top:40px;text-align:center;color:var(--white);font-size:21px;letter-spacing:.5px;font-weight:400}
.popup-rule{left:429px;top:70px;width:60px;height:6px;border-top:2px solid #cfcfcf;border-bottom:1px solid #888}
.popup-close{left:856px;top:38px;width:26px;height:26px}
.partner{left:0;width:918px;top:96px;display:flex;justify-content:center;align-items:center;gap:6px;color:#9a9a9a;font-size:12px}
.partner-dot{width:12px;height:12px;border-radius:50%;background:#9a9a9a}
.field{top:153px;width:199px;height:31px;border:1px solid var(--field-line);color:#e0e0e0;font-size:11px;padding:8px 12px;white-space:nowrap}
.submit-btn{left:397px;top:217px;width:123px;height:37px;background:var(--button-blue);color:var(--ink);font-size:12px;text-align:center;line-height:37px}

/* listing search */
.listing-search{left:141px;top:566px;width:918px;height:54px;background:rgba(10,10,10,.82);display:flex;align-items:center;gap:10px;padding:0 12px}
.search-field{height:32px;border:1px solid var(--field-line);color:#d8d8d8;font-size:11px;padding:9px 12px;white-space:nowrap;flex:0 0 auto}
.search-btn{height:32px;width:150px;background:var(--silver);color:var(--ink);font-size:12px;letter-spacing:.5px;text-align:center;line-height:32px;flex:0 0 auto}

/* welcome */
.welcome-title{left:0;width:1200px;top:750px;text-align:center;font-size:36px;color:#8c8c8c;font-weight:400}
.welcome-copy{left:126px;width:948px;text-align:center;font-size:13.5px;line-height:27px;color:var(--body-text)}
.learn-more{left:528px;top:1041px;width:144px;height:43px;border:1px solid var(--ink);background:var(--ink);text-align:center;line-height:41px;font-size:16px;color:var(--white)}

/* properties */
.section-title{left:0;width:1200px;text-align:center;font-size:36px;color:#8c8c8c;font-weight:400}
.title-rule{width:44px;height:5px;border-top:2px solid #9a9a9a;border-bottom:1px solid #d0d0d0}
.property{width:231px;height:193px}
.property-label{left:0;width:231px;text-align:center;color:var(--white)}

/* feature */
.feature{left:0;top:1802px;width:1200px;height:335px;background:linear-gradient(180deg,#3a3d42 0%,#2f3033 55%,#24231f 100%)}
.feature-title{left:0;width:1200px;top:96px;text-align:center;color:var(--white);font-size:36px;font-weight:400}
.feature-copy{left:160px;width:880px;top:164px;text-align:center;color:#e4e4e4;font-size:15px;line-height:32px}

/* footer */
.site-footer{left:0;top:2137px;width:1200px;height:377px;background:var(--footer-bg)}
.footer-brand{left:100px;top:116px;color:var(--white);font-size:22px;display:flex;align-items:center;gap:10px}
.footer-about{left:100px;top:170px;width:245px;font-size:9px;line-height:14px;color:var(--footer-text)}
.footer-heading{color:var(--white);font-size:13px;letter-spacing:.5px}
.footer-heading-rule{width:40px;height:4px;border-top:2px solid #d0d0d0;border-bottom:1px solid #555}
.footer-link{font-size:12px;color:var(--footer-text);white-space:nowrap}
.contact-icon{width:12px;height:12px}
.footer-divider{left:100px;top:307px;width:1000px;height:1px;background:var(--rule)}
.copyright{left:0;width:1200px;top:334px;text-align:center;font-size:11px;color:var(--footer-text)}
.page-code{left:1136px;top:334px;font-size:11px;color:var(--footer-text)}
</style>
</head>
<body>

<div class="abs hero" role="img" aria-label="Photo of a large stone-and-stucco suburban home with a curved front walkway and lawn"></div>
<svg class="abs hero-curve" viewBox="0 0 1200 140" preserveAspectRatio="none"><path d="M0 134 Q600 10 1200 134 L1200 140 L0 140 Z" fill="#ffffff"/></svg>

<header class="abs site-header">
  <div class="abs brand"><span>HEARTHSTONE</span><span class="brand-mark"></span></div>
  <nav class="main-nav">
    <a class="current" style="left:505px">HOME</a>
    <a style="left:598px">QENO INFO</a>
    <a style="left:713px">ABOUT QE NO HOME</a>
    <a style="left:887px">DOWNLOADS</a>
    <a style="left:1022px">CONTACT US</a>
  </nav>
</header>

<svg class="abs slide-arrow" style="left:30px" viewBox="0 0 20 32"><path d="M16 2 L4 16 L16 30" fill="none" stroke="#e4e4e4" stroke-width="2"/></svg>
<svg class="abs slide-arrow" style="left:1150px" viewBox="0 0 20 32"><path d="M4 2 L16 16 L4 30" fill="none" stroke="#e4e4e4" stroke-width="2"/></svg>

<section class="abs analysis-popup">
  <h2 class="abs popup-title">MY FREE MARKET ANALYSIS</h2>
  <div class="abs popup-rule"></div>
  <svg class="abs popup-close" viewBox="0 0 26 26"><path d="M4 4 L22 22 M22 4 L4 22" stroke="#4a4a4a" stroke-width="5"/></svg>
  <div class="abs partner"><span class="partner-dot"></span><span>Postbird</span></div>
  <div class="abs field" style="left:38px">Full Name</div>
  <div class="abs field" style="left:251px">Email Address</div>
  <div class="abs field" style="left:465px">Phone Number</div>
  <div class="abs field" style="left:680px">Address</div>
  <div class="abs submit-btn">SUBMIT NOW</div>
</section>

<form class="abs listing-search" aria-label="Search active listings">
  <div class="search-field" style="width:250px">City, Zip or MLS #</div>
  <div class="search-field" style="width:150px">Min Price $400,000</div>
  <div class="search-field" style="width:130px">Max Price</div>
  <div class="search-field" style="width:85px">Beds</div>
  <div class="search-field" style="width:85px">Baths</div>
  <div class="search-btn">SEARCH LISTINGS</div>
</form>

<h1 class="abs welcome-title">Welcome to Hearthstone Realty Group</h1>
<p class="abs welcome-copy" style="top:821px">Lorem ipsum dolor sit amet, consectetur adipiscing elit, sed do eiusmod tempor incididunt ut labore et dolore magna aliqua. Ut enim ad minim veniam, quis nostrud exercitation ullamco laboris nisi ut aliquip ex ea commodo consequat. Duis aute irure dolor in reprehenderit in voluptate velit esse cillum dolore eu fugiat nulla pariatur.</p>
<p class="abs welcome-copy" style="top:925px">Sed ut perspiciatis unde omnis iste natus error sit voluptatem accusantium doloremque laudantium, totam rem aperiam, eaque ipsa quae ab illo inventore veritatis et quasi architecto beatae vitae dicta sunt explicabo.</p>
<div class="abs learn-more">Learn more</div>

<h2 class="abs section-title" style="top:1214px">Our Properties</h2>
<div class="abs title-rule" style="left:578px;top:1258px"></div>

<div class="abs property" style="left:99px;top:1307px;background:#2a2a2a" role="img" aria-label="Photo of a featured home, shown under a dark hover overlay">
  <div class="abs property-label" style="top:52px;font-size:25px;letter-spacing:2px">CALIFORNIA</div>
  <div class="abs property-label" style="top:90px;font-size:15px;letter-spacing:1px">14 Linden Street</div>
  <div class="abs property-label" style="top:116px;font-size:15px;letter-spacing:1px">Price on request</div>
</div>
<div class="abs property" style="left:355px;top:1307px;background:linear-gradient(180deg,#b9c6d1 0%,#9c7f70 50%,#6f8a58 100%)" role="img" aria-label="Photo of a brick two-storey house with a green lawn"></div>
<div class="abs property" style="left:612px;top:1307px;background:linear-gradient(180deg,#6d8a55 0%,#6f6f60 50%,#a9bccb 100%)" role="img" aria-label="Photo of a lake house on a wooded shoreline"></div>
<div class="abs property" style="left:868px;top:1307px;background:linear-gradient(180deg,#d7aeb0 0%,#8f7f7a 45%,#6d5a3f 100%)" role="img" aria-label="Photo of a hillside timber home at dusk"></div>
<div class="abs property" style="left:99px;top:1522px;background:linear-gradient(180deg,#dfe2e2 0%,#a08a77 50%,#6c7f52 100%)" role="img" aria-label="Photo of a craftsman bungalow with a brick porch"></div>
<div class="abs property" style="left:355px;top:1522px;background:linear-gradient(180deg,#8a9b7c 0%,#a38d7c 50%,#6a8550 100%)" role="img" aria-label="Photo of a brick family home with a garage"></div>
<div class="abs property" style="left:612px;top:1522px;background:linear-gradient(180deg,#7f9668 0%,#9c6f6a 50%,#66804e 100%)" role="img" aria-label="Photo of a red house among tall trees"></div>
<div class="abs property" style="left:868px;top:1522px;background:linear-gradient(180deg,#c9d7de 0%,#a99675 50%,#8fb3c0 100%)" role="img" aria-label="Photo of a large home beside a pond"></div>

<section class="abs feature" role="img" aria-label="Photo of a grand mansion with balconies and towers">
  <h2 class="abs feature-title">Feature Projects</h2>
  <p class="abs feature-copy">At vero eos et accusamus et iusto odio dignissimos ducimus qui blanditiis praesentium voluptatum deleniti atque corrupti quos dolores et quas molestias excepturi sint occaecati cupiditate non provident</p>
</section>

<footer class="abs site-footer">
  <div class="abs footer-brand"><span>HEARTHSTONE</span><span class="brand-mark"></span></div>
  <p class="abs footer-about">Hearthstone brings you a curated list of fine Midwest homes, lake retreats and estates, with trusted local guidance at every step.</p>

  <div class="abs footer-heading" style="left:449px;top:64px">QUICK LINKS</div>
  <div class="abs footer-heading-rule" style="left:449px;top:88px"></div>
  <div class="abs footer-link" style="left:449px;top:120px">Home</div>
  <div class="abs footer-link" style="left:449px;top:149px">Qeno Info</div>
  <div class="abs footer-link" style="left:449px;top:177px">About Qe No Home</div>
  <div class="abs footer-link" style="left:449px;top:206px">Downloads</div>
  <div class="abs footer-link" style="left:449px;top:234px">Contact Us</div>
  <div class="abs footer-link" style="left:645px;top:120px">Terms &amp; Conditions</div>
  <div class="abs footer-link" style="left:645px;top:149px">Privacy Policy</div>
  <div class="abs footer-link" style="left:645px;top:177px">Contact</div>

  <div class="abs footer-heading" style="left:858px;top:64px">CONTACT US</div>
  <div class="abs footer-heading-rule" style="left:858px;top:88px"></div>
  <svg class="abs contact-icon" style="left:858px;top:122px" viewBox="0 0 12 12"><path d="M6 0 A4 4 0 0 1 10 4 C10 7 6 12 6 12 C6 12 2 7 2 4 A4 4 0 0 1 6 0 Z" fill="#c9c9c9"/><circle cx="6" cy="4" r="1.5" fill="#111111"/></svg>
  <div class="abs footer-link" style="left:880px;top:120px">Hearthstone Realty Group</div>
  <div class="abs footer-link" style="left:880px;top:149px">Street Address, City Name, Country</div>
  <svg class="abs contact-icon" style="left:858px;top:179px" viewBox="0 0 12 12"><path d="M2.5 0.5 L4.5 3 L3.3 4.6 C4 6.2 5.8 8 7.4 8.7 L9 7.5 L11.5 9.5 L10.2 11.5 C5 11 1 7 0.5 1.8 Z" fill="#c9c9c9"/></svg>
  <div class="abs footer-link" style="left:880px;top:177px">0190 555 0142</div>
  <svg class="abs contact-icon" style="left:858px;top:208px" viewBox="0 0 12 12"><rect x="0" y="2" width="12" height="8" fill="#c9c9c9"/><path d="M0 2 L6 7 L12 2" fill="none" stroke="#111111" stroke-width="1"/></svg>
  <div class="abs footer-link" style="left:880px;top:206px">info@hearthstonerealty.com</div>
  <svg class="abs contact-icon" style="left:858px;top:236px" viewBox="0 0 12 12"><circle cx="6" cy="6" r="6" fill="#c9c9c9"/><path d="M0 6 H12 M6 0 C3 3 3 9 6 12 M6 0 C9 3 9 9 6 12" fill="none" stroke="#111111" stroke-width=".8"/></svg>
  <div class="abs footer-link" style="left:880px;top:234px">www.hearthstonerealty.com</div>

  <div class="abs footer-divider"></div>
  <div class="abs copyright">© 2018 HEARTHSTONE REALTY GROUP . All rights reserved . Term of Use</div>
  <div class="abs page-code">C16</div>
</footer>

</body>
</html>
```